MV Decor

There is a sample provided with the arabic text of the business card. please copy paste the same text and the same Logo (The two triangles) Just try to incorproate the Brown background attached (you are free to change the colors) Id like the colors to be mainly shades of black and red.

```html
<!DOCTYPE html>
<html lang="ar">
<head>
<meta charset="utf-8">
<title>MV Decor – Business Card</title>
<link href="https://fonts.googleapis.com/css2?family=Tajawal:wght@400;500;700;800&family=Aref+Ruqaa:wght@400;700&display=swap" rel="stylesheet">
<style>
  :root {
    --page-bg: #e9e6e2;
    --red: #d8234a;
    --red-deep: #b81a3d;
    --red-light: #e4436a;
    --black: #141414;
    --black-soft: #2c2c2c;
    --white: #ffffff;
    --shadow: rgba(0,0,0,0.35);
  }
  * { margin: 0; padding: 0; box-sizing: border-box; }
  html, body {
    width: 1125px; height: 1200px; overflow: hidden;
    background: var(--page-bg);
  }
  .canvas { position: relative; width: 1125px; height: 1200px; }
  .card {
    position: absolute; left: 150px; width: 826px; height: 472px;
    overflow: hidden; box-shadow: 0 4px 10px var(--shadow);
    font-family: "Tajawal", sans-serif; color: var(--white);
  }
  .card--front { top: 106px; }
  .card--back { top: 640px; }

  .front-red {
    position: absolute; inset: 0;
    background: radial-gradient(ellipse at 70% 40%, var(--red-light) 0%, var(--red) 45%, var(--red-deep) 100%);
  }
  .front-dark {
    position: absolute; inset: 0;
    background: radial-gradient(ellipse at 45% 35%, var(--black-soft) 0%, var(--black) 70%);
    clip-path: polygon(0 0, 41% 0, 69.5% 100%, 0 100%);
  }

  .profile__name, .profile__role, .profile__quals {
    position: absolute; right: calc(100% - 287px);
    direction: rtl; text-align: right; white-space: nowrap;
  }
  .profile__name {
    top: 172px;
    font-family: "Aref Ruqaa", serif; font-weight: 700; font-size: 27px; line-height: 1.1;
  }
  .profile__role {
    top: 215px; right: calc(100% - 228px);
    font-family: "Aref Ruqaa", serif; font-size: 17px; line-height: 1.1;
  }
  .profile__quals {
    top: 262px; list-style: none; font-size: 22px; line-height: 28px;
  }
  .profile__phone {
    position: absolute; left: 56px; top: 394px;
    direction: ltr; white-space: nowrap;
    font-size: 21px; font-weight: 500; line-height: 24px;
    display: flex; align-items: center; gap: 6px;
  }
  .profile__phone svg { width: 19px; height: 19px; fill: var(--white); flex: none; }

  .brand {
    position: absolute; left: 541px; top: 252px; width: 200px;
    text-align: center; font-weight: 800; font-size: 38px; line-height: 1;
    letter-spacing: 1px; color: var(--white); white-space: nowrap;
  }

  .back-bg {
    position: absolute; inset: 0;
    background: linear-gradient(100deg, var(--red) 0%, var(--red) 55%, var(--red-light) 80%, var(--red) 100%);
  }
  .services {
    position: absolute; top: 99px; right: calc(100% - 387px); width: 300px;
    list-style: none; direction: rtl; font-size: 27px; line-height: 33px;
  }
  .services__item { display: flex; align-items: center; white-space: nowrap; }
  .services__item::after {
    content: ""; width: 9px; height: 9px; border-radius: 50%;
    background: var(--black); flex: none; margin-right: auto;
  }
</style>
</head>
<body>
<main class="canvas">
  <section class="card card--front">
    <div class="front-red" role="img" aria-label="Red background with a soft square-grid texture"></div>
    <div class="front-dark" role="img" aria-label="Black diagonal panel with a soft square-grid texture"></div>
    <p class="profile__name">المهندس / أحمد سالم الراشد</p>
    <p class="profile__role">أستاذ جامعي</p>
    <ul class="profile__quals">
      <li>ماجستير هندسة ديكور</li>
      <li>دبلوم عالي فن تشكيلي</li>
      <li>أكاديمية الفنون (باريس)</li>
      <li>استشارات هندسية - فنية</li>
    </ul>
    <p class="profile__phone">
      <svg viewBox="0 0 24 24" aria-hidden="true"><path d="M6.6 10.8a15.2 15.2 0 0 0 6.6 6.6l2.2-2.2a1 1 0 0 1 1-.25 11.4 11.4 0 0 0 3.6.57 1 1 0 0 1 1 1V20a1 1 0 0 1-1 1A17 17 0 0 1 3 4a1 1 0 0 1 1-1h3.5a1 1 0 0 1 1 1c0 1.25.2 2.45.57 3.6a1 1 0 0 1-.25 1z"/></svg>
      31245870 / 65538214
    </p>
    <div class="brand">MV DECOR</div>
  </section>

  <section class="card card--back">
    <div class="back-bg" role="img" aria-label="Red background with a soft square-grid texture"></div>
    <ul class="services">
      <li class="services__item">ماجستير هندسة ديكور</li>
      <li class="services__item">دبلوم عالي فن تشكيلي</li>
      <li class="services__item">أكاديمية الفنون (باريس)</li>
      <li class="services__item">استشارات هندسية - فنية</li>
      <li class="services__item">ماجستير هندسة ديكور</li>
      <li class="services__item">دبلوم عالي فن تشكيلي</li>
      <li class="services__item">أكاديمية الفنون (باريس)</li>
      <li class="services__item">استشارات هندسية - فنية</li>
    </ul>
  </section>
</main>
</body>
</html>
```